Retail/Wholesale website graphic template

I need to design a new graphic template for a website for a client. The website will be a retail/wholesale company site with most pages dedicated to presentation. There will also be an online store and a blog. However, you don't need to worry about those. All I need from you is a graphic template for a generic site page.

It will need to include standard UI elements, in case I need those. I am attaching a more detailed assignment in .docx format.

The logo is also attached.

Target Market(s)

small business owners, (occasional) retail customers

Industry/Entity Type

Wholesale

Number of Pages Required

1 page

Font styles to use
Serif
Sans Serif

Colors
ec1f27
474747

Requirements
Must have
• must match logo, be clean, minimal and with slightly larger text size
Should not have
• must not be modern-looking where you have to scroll and scroll and scroll to get to the bottom of the homepage. most of my visitors are "old" people, they do not get this type of design.

```html
<!DOCTYPE html>
<html lang="en">
<head>
<meta charset="utf-8">
<title>Harbor Imports</title>
<link href="https://fonts.googleapis.com/css2?family=Lato:wght@400;700;900&display=swap" rel="stylesheet">
<style>
:root{
  --red:#ec1f27;
  --ink:#111;
  --grey:#474747;
  --muted:#777;
  --light:#f1f1f1;
  --dark:#111;
  --white:#fff;
}
*{margin:0;padding:0;box-sizing:border-box}
html,body{width:1200px;height:3279px;overflow:hidden}
body{font-family:'Lato',sans-serif;color:var(--grey);background:var(--white);position:relative}
.abs{position:absolute}
.topbar{top:0;left:0;width:1200px;height:44px;background:var(--red);color:#fff;font-size:13px;font-weight:700}
.topbar .contact{left:98px;top:14px;display:flex;gap:26px;align-items:center}
.topbar .login{right:0;top:0;width:225px;height:44px;background:#2b2b2b;display:flex;align-items:center;justify-content:center;gap:8px;letter-spacing:.5px}
.header{top:44px;left:0;width:1200px;height:116px;background:#fff}
.brand{left:98px;top:28px;width:182px;height:64px;border:3px solid var(--ink);display:flex;align-items:center;justify-content:center;font-weight:900;font-size:30px;letter-spacing:1px;color:var(--ink)}
.nav{right:98px;top:50px;display:flex;gap:36px;font-size:15px;font-weight:700;color:var(--ink);align-items:center}
.hero{top:160px;left:0;width:1200px;height:557px;background:linear-gradient(135deg,#b38a63,#8c6a4d 40%,#c4a07a 70%,#6e5240);border-bottom:5px solid var(--red)}
.hero h1{position:absolute;top:190px;width:100%;text-align:center;color:#fff;font-weight:900;font-size:70px;text-shadow:0 2px 6px rgba(0,0,0,.4)}
.hero p{position:absolute;top:285px;left:270px;width:660px;text-align:center;color:#fff;font-size:21px;font-weight:700;line-height:1.45;text-shadow:0 1px 4px rgba(0,0,0,.5)}
.slider-tab{top:682px;left:507px;width:184px;height:46px;background:#fff;border:4px solid var(--red);border-bottom:none;display:flex;gap:8px;justify-content:center;align-items:center;padding-top:4px}
.dot{width:15px;height:15px;border-radius:50%;border:2px solid var(--grey)}
.dot.on{background:var(--red);border-color:var(--red)}
h2{font-weight:900;font-size:30px;color:var(--ink);letter-spacing:.3px}
.excellence h2{position:absolute;left:98px;top:812px}
.lead{left:98px;top:878px;width:500px;color:var(--red);font-weight:700;font-size:19px;line-height:1.5}
.body-text{font-size:13px;line-height:1.85;color:var(--muted)}
.ex-text{left:98px;top:950px;width:490px;text-align:justify}
.btn{left:98px;top:1095px;width:140px;height:40px;background:var(--red);color:#fff;border-radius:20px;font-size:13px;font-weight:700;display:flex;align-items:center;justify-content:center;gap:6px}
.video-frame{left:682px;top:813px;width:453px;height:273px;border:3px solid var(--red)}
.video{left:647px;top:848px;width:448px;height:271px;background:linear-gradient(120deg,#3b4a8c,#c79a63 45%,#d8b07c 70%,#e3b832);box-shadow:0 2px 10px rgba(0,0,0,.25)}
.play{left:844px;top:955px}
.services{top:1231px;left:0;width:1200px;height:540px;background:linear-gradient(180deg,#2e3236,#4a4c4f 50%,#3a3c3e)}
.services h2{position:absolute;top:92px;width:100%;text-align:center;color:#fff}
.services .intro{position:absolute;top:140px;left:290px;width:620px;text-align:center;color:#eee;font-size:13px;line-height:2}
.svc{top:1465px;width:481px;height:214px;background:#fff;display:flex}
.svc .img{width:193px;height:214px}
.svc .info{padding:30px 26px}
.svc h3{font-size:18px;font-weight:700;color:var(--ink);margin-bottom:14px}
.svc p{font-size:12px;line-height:1.9;color:var(--muted);margin-bottom:14px}
.more{color:var(--red);font-size:12px;font-weight:700}
.boxes{left:98px;top:1858px;width:438px;height:335px;background:linear-gradient(135deg,#e0b67f,#c58f54 55%,#a87442)}
.products h2{position:absolute;left:636px;top:1857px}
.pr-text{left:636px;top:1922px;width:464px;text-align:justify}
.checks{left:636px;top:2030px;width:464px;display:grid;grid-template-columns:219px 245px;row-gap:22px;font-size:13px;color:var(--muted)}
.checks span{display:flex;align-items:center;gap:10px}
.news{top:2247px;left:0;width:1200px;height:606px;background:var(--light)}
.news h2{position:absolute;top:70px;width:100%;text-align:center}
.news .sub{position:absolute;top:128px;width:100%;text-align:center;font-size:13px;color:var(--grey)}
.card{top:2433px;width:313px}
.card .img{height:186px;position:relative}
.date{position:absolute;left:16px;top:0;width:46px;height:52px;background:var(--red);color:#fff;text-align:center;font-size:11px;padding-top:6px}
.date b{display:block;font-size:17px}
.card h4{margin-top:22px;font-size:18px;font-weight:700;color:var(--ink);line-height:1.45}
.meta{margin-top:12px;font-size:12px;color:var(--muted);display:flex;gap:14px;align-items:center}
.card p{margin-top:10px;font-size:12px;line-height:1.9;color:var(--muted)}
.footer{top:2853px;left:0;width:1200px;height:426px;background:var(--dark);border-top:4px solid var(--red);color:#fff}
.fcol{top:68px}
.fcol h5{font-size:15px;font-weight:700;margin-bottom:20px;letter-spacing:.3px}
.fcol li{list-style:none;font-size:12px;margin-bottom:15px;display:flex;align-items:center;gap:8px}
.fcol li::before{content:"»";font-size:12px}
.fcol.contact li::before{content:none}
.fbrand{left:98px;top:243px;width:172px;height:58px;border:3px solid #fff;display:flex;align-items:center;justify-content:center;font-weight:900;font-size:26px;letter-spacing:1px}
.social{right:98px;top:262px;display:flex;gap:14px}
.social i{width:20px;height:20px;border-radius:50%;background:#fff;display:block}
.rule{left:98px;top:341px;width:1004px;height:1px;background:#444}
.copy{top:383px;width:100%;text-align:center;font-size:12px;color:#ddd}
</style>
</head>
<body>

<div class="abs topbar">
  <div class="abs contact">
    <span>&#9742; (+01) 555 014 2280</span>
    <span>&#9993; info@harborimports.com</span>
  </div>
  <div class="abs login">
    <svg width="11" height="13" viewBox="0 0 11 13"><rect x="1" y="5" width="9" height="7" fill="#fff"/><path d="M3 5V3.5a2.5 2.5 0 0 1 5 0V5" stroke="#fff" stroke-width="1.6" fill="none"/></svg>
    LOGIN
  </div>
</div>

<header class="abs header">
  <div class="abs brand">HARBOR</div>
  <nav class="abs nav">
    <span>HOME</span><span>ABOUT US</span><span>SERVICES</span><span>PRODUCTS</span><span>NEWS</span><span>CONTACT US</span>
    <svg width="15" height="15" viewBox="0 0 15 15"><circle cx="6" cy="6" r="4.5" stroke="#111" stroke-width="2" fill="none"/><path d="M9.5 9.5L14 14" stroke="#111" stroke-width="2"/></svg>
  </nav>
</header>

<section class="abs hero" role="img" aria-label="Clothing store interior with garments on racks and shelves">
  <h1>HARBOR IMPORTS</h1>
  <p>Nam libero tempore, cum soluta nobis est eligendi optio cumque nihil impedit quo minus id quod maxime placeat facere</p>
</section>
<div class="abs slider-tab">
  <span class="dot"></span><span class="dot"></span><span class="dot on"></span><span class="dot"></span><span class="dot"></span>
</div>

<section class="excellence">
  <h2>EXCELLENCE IN IMPORT</h2>
  <p class="abs lead">We specialize in retail &amp; whole sale import and offer a full range import services.</p>
  <p class="abs body-text ex-text">At vero eos et accusamus et iusto odio dignissimos ducimus qui blanditiis praesentium voluptatum deleniti atque corrupti quos dolores et quas molestias excepturi sint occaecati cupiditate non provident, similique sunt in culpa qui officia deserunt mollitia animi, id est laborum et dolorum fuga. Et harum quidem rerum facilis est et expedita distinctio libero tempore.</p>
  <div class="abs btn">READ MORE <svg width="12" height="12" viewBox="0 0 12 12"><circle cx="6" cy="6" r="6" fill="#fff"/><path d="M5 3.5L7.5 6 5 8.5" stroke="#ec1f27" stroke-width="1.6" fill="none"/></svg></div>
  <div class="abs video-frame"></div>
  <div class="abs video" role="img" aria-label="Video still of hands passing a cardboard parcel in a warehouse"></div>
  <svg class="abs play" width="56" height="56" viewBox="0 0 56 56"><circle cx="28" cy="28" r="28" fill="#ec1f27"/><path d="M22 17L40 28 22 39z" fill="#fff"/></svg>
</section>

<section class="abs services" role="img" aria-label="Delivery truck loaded with cardboard boxes, darkened">
  <h2>OUR SERVICES</h2>
  <p class="intro">At vero eos et accusamus et iusto odio dignissimos ducimus qui blanditiis praesentium voluptatum deleniti atque corrupti quos dolores et quas molestias excepturi sint</p>
</section>
<div class="abs svc" style="left:98px">
  <div class="img" role="img" aria-label="Colourful sneakers on display" style="background:linear-gradient(135deg,#c53b3b,#3d4f9a 55%,#e07bb0)"></div>
  <div class="info">
    <h3>RETAIL SERVICES</h3>
    <p>At vero eos et accusam muset iusto odio dignissimos ducimus qu praeseum tre voluptatum deleniti atque</p>
    <span class="more">READ MORE &#10140;</span>
  </div>
</div>
<div class="abs svc" style="left:619px">
  <div class="img" role="img" aria-label="Cardboard boxes on a conveyor" style="background:linear-gradient(135deg,#d4a46a,#a9773f 60%,#5a4a3a)"></div>
  <div class="info">
    <h3>WHOLE SALE IMPORT</h3>
    <p>At vero eos et accusam muset iusto odio dignissimos ducimus qu praeseum tre voluptatum deleniti atque</p>
    <span class="more">READ MORE &#10140;</span>
  </div>
</div>

<section class="products">
  <div class="abs boxes" role="img" aria-label="Stack of three cardboard shipping boxes"></div>
  <h2>OUR PRODUCTS</h2>
  <p class="abs body-text pr-text">At vero eos et accusamus et iusto odio dignissimos ducimus qui blanditiis praesentium voluptatum deleniti atque corrupti quos dolores et quas molestias excepturi sint occaecati cupiditate non provident.</p>
  <div class="abs checks">
    <span><svg width="16" height="14" viewBox="0 0 16 14"><path d="M1 7l5 5L15 1" stroke="#ec1f27" stroke-width="2" fill="none"/></svg>100% Safe &amp; Secure</span>
    <span><svg width="16" height="14" viewBox="0 0 16 14"><path d="M1 7l5 5L15 1" stroke="#ec1f27" stroke-width="2" fill="none"/></svg>Customs Consultancy</span>
    <span><svg width="16" height="14" viewBox="0 0 16 14"><path d="M1 7l5 5L15 1" stroke="#ec1f27" stroke-width="2" fill="none"/></svg>Safe Delivery</span>
    <span><svg width="16" height="14" viewBox="0 0 16 14"><path d="M1 7l5 5L15 1" stroke="#ec1f27" stroke-width="2" fill="none"/></svg>Secure Payments</span>
    <span><svg width="16" height="14" viewBox="0 0 16 14"><path d="M1 7l5 5L15 1" stroke="#ec1f27" stroke-width="2" fill="none"/></svg>Import Documents</span>
    <span><svg width="16" height="14" viewBox="0 0 16 14"><path d="M1 7l5 5L15 1" stroke="#ec1f27" stroke-width="2" fill="none"/></svg>Whole Sale Import</span>
  </div>
</section>

<section class="abs news">
  <h2>LATEST NEWS</h2>
  <p class="sub">Read The Latest News Regarding Our Retail &amp; Whole Sale Import Service.</p>
</section>
<article class="abs card" style="left:98px">
  <div class="img" role="img" aria-label="Shop shelves stocked with colourful bottles" style="background:linear-gradient(135deg,#e8b04a,#d05a6b 50%,#6aa0c8)"><div class="date">May<b>12</b></div></div>
  <h4>Minus id quod maxime placeat Facere possimus</h4>
  <div class="meta"><span style="color:#ec1f27">&#9679;</span> Anika &nbsp;|&nbsp; <span style="color:#ec1f27">&#9993;</span> 214 Comments</div>
  <p>Nam libero tempore, cum soluta nobis est eligendi optio cumque nihil impedit quo minus</p>
</article>
<article class="abs card" style="left:444px">
  <div class="img" role="img" aria-label="Folded jeans stacked on store shelves" style="background:linear-gradient(135deg,#2f3b55,#5a6f95 50%,#8a7a68)"><div class="date">May<b>12</b></div></div>
  <h4>Minus id quod maxime placeat Facere possimus</h4>
  <div class="meta"><span style="color:#ec1f27">&#9679;</span> Anika &nbsp;|&nbsp; <span style="color:#ec1f27">&#9993;</span> 214 Comments</div>
  <p>Nam libero tempore, cum soluta nobis est eligendi optio cumque nihil impedit quo minus</p>
</article>
<article class="abs card" style="left:787px">
  <div class="img" role="img" aria-label="Warehouse worker checking stacked boxes with a tablet" style="background:linear-gradient(135deg,#2a2a2a,#7a5a3a 50%,#c49560)"><div class="date">May<b>12</b></div></div>
  <h4>Minus id quod maxime placeat Facere possimus</h4>
  <div class="meta"><span style="color:#ec1f27">&#9679;</span> Anika &nbsp;|&nbsp; <span style="color:#ec1f27">&#9993;</span> 214 Comments</div>
  <p>Nam libero tempore, cum soluta nobis est eligendi optio cumque nihil impedit quo minus</p>
</article>

<footer class="abs footer">
  <div class="abs fcol" style="left:98px">
    <h5>PRODUCT GALLERY</h5>
    <ul><li>Our Products</li><li>Import Products</li><li>Retail Products</li><li>Whole Sale.</li></ul>
  </div>
  <div class="abs fcol" style="left:383px">
    <h5>QUICK LINKS</h5>
    <ul><li>Home</li><li>About Us</li><li>Services</li><li>Contact Us</li></ul>
  </div>
  <div class="abs fcol" style="left:647px">
    <h5>RETAILS INSIGHTS</h5>
    <ul><li>News</li><li>Blog Post</li><li>Our Story</li><li>FAQ</li></ul>
  </div>
  <div class="abs fcol contact" style="left:925px">
    <h5>CONTACT US</h5>
    <ul>
      <li>&#9679;&nbsp; 48 Quay Lane, Dockside<br>&nbsp;&nbsp;&nbsp;&nbsp;&nbsp;ZX4 7PL</li>
      <li>&#9742;&nbsp; (+01) 555 014 2280</li>
      <li>&#9993;&nbsp; info@harborimports.com</li>
    </ul>
  </div>
  <div class="abs fbrand">HARBOR</div>
  <div class="abs social"><i></i><i></i><i></i><i></i><i></i><i></i><i></i></div>
  <div class="abs rule"></div>
  <p class="abs copy">© Copyright 2018 Harbor Imports. All Rights Reserved &nbsp;&nbsp;|&nbsp;&nbsp; Privacy Policy &nbsp;&nbsp;|&nbsp;&nbsp; Site Map.</p>
</footer>

</body>
</html>
```